Job Recruiting Agemcy

almost like my current site www.plorvex.com but with these changes see and what i meant about the across the to the site says home job companies categories pages blog and login sign up that should only be the 4 i said only 1 home 2 industries 3 jobs 4 contact us. and remove latest blog post and our partners because that's not us we have to post acuarte information thanks and the name of the company if your using is is work and careful hiring partners and want it easy for us to post and remove jobs and where it emails us every resume or person that applies

Requirements
Must have
• must send email to us when an application is submitted and try to incorparate the colors of current site
Nice to have
• i want a pretty basic site for now just like the one i have but with all thats above were its easy for me being the own to be able to post jobs and everything

```html
<!DOCTYPE html>
<html lang="en">
<head>
<meta charset="utf-8">
<title>Plorvex – Work and Careful Hiring Partners</title>
<link href="https://fonts.googleapis.com/css2?family=Ubuntu:wght@400;500&family=Varela+Round&display=swap" rel="stylesheet">
<style>
:root{
  --green:#2f6446;
  --green-dark:#285a3d;
  --ink:#1d1d1d;
  --muted:#3a3a3a;
  --grey:#f2f2f2;
  --card:#f3f3f3;
  --footer:#111111;
  --white:#ffffff;
  --red:#d82020;
  --amber:#f2c320;
  --hero-a:#6f8b8e;
  --hero-b:#3d5c63;
}
*{box-sizing:border-box;margin:0;padding:0}
html,body{width:1200px;height:3190px;overflow:hidden}
body{position:relative;font-family:'Ubuntu',sans-serif;color:var(--ink);background:var(--white)}
.abs{position:absolute}
.body-font{font-family:'Varela Round',sans-serif}

.topbar{left:0;top:0;width:1200px;height:52px;background:var(--green);color:var(--white);font-size:19px}
.topbar .item{top:14px;display:flex;align-items:center;gap:12px}
.topbar .dots{right:90px;top:19px;display:flex;gap:30px}
.topbar .dots span{width:12px;height:12px;border-radius:50%;background:var(--white);opacity:.85}

.nav-logo{left:89px;top:52px;width:119px;height:123px;background:#f1f1f1;display:flex;align-items:center;justify-content:center;font-size:22px;font-weight:500;color:var(--ink)}
.nav-links{top:106px;left:320px;display:flex;gap:52px;font-size:19px;text-transform:uppercase}
.nav-links a{color:var(--ink);text-decoration:none}
.nav-links a.active{color:var(--green)}
.btn{display:flex;align-items:center;justify-content:center;border-radius:5px;text-transform:uppercase}
.btn-solid{background:var(--green);color:var(--white)}
.btn-outline{border:3px solid var(--green);color:var(--ink);background:var(--white)}
.login{left:915px;top:89px;width:192px;height:58px;font-size:17px}

.hero{left:0;top:175px;width:1200px;height:582px;background:linear-gradient(100deg,var(--hero-a) 0%,#58777d 55%,var(--hero-b) 100%)}
.hero-person{left:740px;top:175px;width:460px;height:582px;background:linear-gradient(180deg,#2e3c44 0%,#1c2328 100%);border-radius:200px 0 0 0;opacity:.55}
.hero h2{left:89px;top:355px;font-size:34px;font-weight:400;color:var(--white);letter-spacing:.5px}
.hero h1{left:89px;top:412px;font-size:42px;font-weight:400;color:var(--white)}
.field{top:487px;width:252px;height:45px;background:var(--white);font-family:'Varela Round',sans-serif;font-size:15px;color:#444;padding:12px 12px}
.search-btn{left:633px;top:486px;width:124px;height:48px;font-size:16px}

.welcome h2{left:84px;top:832px;font-size:36px;font-weight:400}
.welcome p{left:86px;top:893px;width:480px;font-size:17px;line-height:30.5px;color:var(--muted)}
.read-more{left:84px;top:1054px;width:165px;height:52px;font-size:17px}
.welcome-photo{left:713px;top:833px;width:394px;height:272px;border-radius:4px;background:linear-gradient(120deg,#6f7f86 0%,#b9c2c6 55%,#8d8a84 100%)}

.section-title{font-size:36px;font-weight:400}
.ind-card{top:1265px;width:328px;height:171px;background:var(--card);border-radius:4px}
.ind-card.on{background:var(--green);color:var(--white)}
.ind-card .icon{left:44px;top:14px;width:64px;height:56px;border-radius:6px;background:#cfd8d3}
.ind-card.on .icon{background:#4f7f63;left:24px}
.ind-card .label{left:46px;bottom:20px;width:220px;font-size:17px;line-height:27px}
.ind-card.on .label{left:24px}
.ind-card .count{right:18px;top:56px;font-size:56px;color:#b8b8b8;font-weight:500}
.ind-card.on .count{color:#9db3a6}

.dots3{display:flex;gap:6px}
.dots3 span{width:12px;height:12px;border-radius:50%;background:var(--green)}
.dots3 span.o{background:var(--white);border:2px solid var(--green)}

.jobs-bg{left:0;top:1577px;width:1192px;height:538px;background:var(--grey)}
.job{left:100px;width:985px;background:var(--white);border-radius:4px}
.job.raised{box-shadow:0 2px 8px rgba(0,0,0,.2)}
.job .title{left:16px;top:30px;font-size:19px;text-transform:uppercase}
.job .meta{left:16px;font-size:15px;display:flex;align-items:center;gap:10px;text-transform:uppercase}
.job .meta.red{color:var(--red)}
.job .pay{left:496px;top:36px;font-size:15px;display:flex;align-items:center;gap:14px}
.job .time{left:496px;top:64px;font-size:16px;display:flex;align-items:center;gap:14px;color:var(--green)}
.job .time.part{color:var(--amber)}
.job .view{left:780px;width:159px;height:53px;font-size:17px}

.testi{top:2273px;width:330px;height:337px;background:var(--white);box-shadow:0 1px 8px rgba(0,0,0,.15);border-radius:3px;text-align:center}
.quote{top:2263px;width:34px;height:34px;background:var(--green);color:var(--white);font-size:22px;font-family:Georgia,serif;display:flex;align-items:center;justify-content:center}
.avatar{left:132px;top:32px;width:68px;height:68px;border-radius:50%;background:linear-gradient(160deg,#d7c3b6,#8f7e75)}
.testi p{left:18px;width:294px;top:126px;font-family:'Varela Round',sans-serif;font-size:13.5px;line-height:27px;color:#3a3a3a}
.testi .name{left:0;width:330px;top:296px;font-size:17px}

.cta{left:0;top:2742px;width:1200px;height:104px;background:var(--green);color:var(--white)}
.cta h3{left:84px;top:18px;font-size:20px;font-weight:400}
.cta p{left:85px;top:46px;width:320px;font-size:13px;line-height:23px}
.cta .b{top:39px;height:40px;background:var(--white);color:var(--ink);border-radius:6px;font-size:15px}

.footer{left:0;top:2846px;width:1200px;height:344px;background:var(--footer);color:var(--white)}
.footer .brand{left:92px;top:86px;font-size:26px;font-weight:500;letter-spacing:1px}
.footer .about{left:91px;top:168px;width:296px;font-size:13.5px;line-height:24px;text-align:justify}
.footer h4{top:56px;font-size:17px;font-weight:400;text-transform:uppercase}
.footer ul{list-style:none;top:100px;font-size:13.5px;line-height:32px}
.footer .legal{left:0;width:1200px;top:302px;text-align:center;font-size:15px;text-transform:uppercase;word-spacing:2px}
</style>
</head>
<body>

<header>
  <div class="topbar abs">
    <div class="item abs" style="left:90px">
      <svg width="16" height="16" viewBox="0 0 16 16"><rect width="16" height="16" rx="2" fill="#fff"/><path d="M4.5 3.5l2 2-1 1.2c.6 1.4 1.6 2.4 3 3l1.2-1 2 2-1.2 1.6c-3.4-.4-6.5-3.5-7-7z" fill="#2f6446"/></svg>
      <span>+1 800 555 0142</span>
    </div>
    <div class="item abs" style="left:313px">
      <svg width="20" height="15" viewBox="0 0 20 15"><rect x="1" y="1" width="18" height="13" rx="2" fill="none" stroke="#fff" stroke-width="1.8"/><path d="M2 2l8 6 8-6" fill="none" stroke="#fff" stroke-width="1.8"/></svg>
      <span>info@plorvex.com</span>
    </div>
    <div class="dots abs"><span></span><span></span><span></span><span></span></div>
  </div>

  <div class="nav-logo abs">Plorvex</div>
  <nav class="nav-links abs">
    <a class="active" href="#">Home</a>
    <a href="#">Industries</a>
    <a href="#">Jobs</a>
    <a href="#">Contact Us</a>
  </nav>
  <div class="login btn btn-solid abs">Log In / Sign Up</div>
</header>

<section class="hero-wrap">
  <div class="hero abs" role="img" aria-label="Hero photo: smiling businesswoman in a dark suit against a teal studio backdrop"></div>
  <div class="hero-person abs" role="img" aria-label="Businesswoman with arms crossed"></div>
  <div class="hero">
    <h2 class="abs">SEARCH&nbsp; FROM&nbsp; JOB OFFERS</h2>
    <h1 class="abs">YOUR CAREER STARTS HERE!</h1>
    <div class="field abs" style="left:89px">Keywords</div>
    <div class="field abs" style="left:361px">Location</div>
    <div class="search-btn btn btn-solid abs">Search</div>
  </div>
</section>

<section class="welcome">
  <h2 class="abs">WELCOME&nbsp; TO PLORVEX</h2>
  <p class="abs body-font">We have over 35 years of Specialized Recruiting and souring experience. We cover a broad spectrum of industries to include some of the top aerospace and pharmaceutical commercial&nbsp; companies of today.</p>
  <div class="read-more btn btn-solid abs">Read More</div>
  <div class="welcome-photo abs" role="img" aria-label="Photo of a recruiter interviewing a candidate across a desk"></div>
</section>

<section class="industries">
  <h2 class="section-title abs" style="left:84px;top:1177px">INDUSTRIES WE SUPPORT</h2>
  <div class="ind-card abs" style="left:84px">
    <div class="icon abs" role="img" aria-label="Aircraft icon"></div>
    <div class="label abs">Aero Space- Corvane Aero Controls, Altira Orbital Brenlow Electric</div>
    <div class="count abs">0</div>
  </div>
  <div class="ind-card on abs" style="left:428px">
    <div class="icon abs" role="img" aria-label="Pills and medicine icon"></div>
    <div class="label abs">Pharmaceutical/ Biotech-nology Vitalis Labs , Marlowe Cosmetics</div>
    <div class="count abs">0</div>
  </div>
  <div class="ind-card abs" style="left:777px">
    <div class="icon abs" role="img" aria-label="Delivery truck icon" style="left:26px;width:86px"></div>
    <div class="label abs" style="left:26px;bottom:34px">Transportation- Halden Freight, Parcelway</div>
    <div class="count abs">0</div>
  </div>
  <div class="dots3 abs" style="left:578px;top:1488px"><span></span><span class="o"></span><span></span></div>
</section>

<section class="jobs">
  <div class="jobs-bg abs"></div>
  <h2 class="section-title abs" style="left:0;width:1192px;text-align:center;top:1603px">RECENT JOBS</h2>

  <div class="job abs" style="top:1678px;height:120px">
    <div class="title abs">Aero Space- Corvane Aero Controls</div>
    <div class="meta abs" style="top:60px"><svg width="12" height="12"><circle cx="6" cy="6" r="6" fill="#222"/></svg>Germany</div>
    <div class="meta red abs" style="top:86px"><svg width="12" height="12"><rect x="1" y="5" width="10" height="7" fill="#222"/><path d="M3 5V3.5a3 3 0 016 0V5" fill="none" stroke="#222" stroke-width="1.6"/></svg>Expired</div>
    <div class="pay abs"><svg width="14" height="10"><rect x=".5" y=".5" width="13" height="9" fill="none" stroke="#222"/><circle cx="7" cy="5" r="2" fill="#222"/></svg>$31000</div>
    <div class="time abs"><svg width="12" height="12"><circle cx="6" cy="6" r="5" fill="none" stroke="currentColor" stroke-width="1.6"/><path d="M6 3v3h2" stroke="currentColor" fill="none"/></svg>Full Time</div>
    <div class="view btn btn-outline abs" style="top:36px">View More</div>
  </div>

  <div class="job raised abs" style="top:1822px;height:112px">
    <div class="title abs">Biotechnology Vitalis Labs</div>
    <div class="meta abs" style="top:60px"><svg width="12" height="12"><circle cx="6" cy="6" r="6" fill="#222"/></svg>Germany</div>
    <div class="pay abs"><svg width="14" height="10"><rect x=".5" y=".5" width="13" height="9" fill="none" stroke="#222"/><circle cx="7" cy="5" r="2" fill="#222"/></svg>$31000</div>
    <div class="time part abs"><svg width="12" height="12"><circle cx="6" cy="6" r="5" fill="none" stroke="currentColor" stroke-width="1.6"/><path d="M6 3v3h2" stroke="currentColor" fill="none"/></svg>Part Time</div>
    <div class="view btn btn-solid abs" style="top:33px">View More</div>
  </div>

  <div class="job abs" style="top:1958px;height:120px">
    <div class="title abs">Transportation- Halden Freight</div>
    <div class="meta abs" style="top:60px"><svg width="12" height="12"><circle cx="6" cy="6" r="6" fill="#222"/></svg>Germany</div>
    <div class="meta red abs" style="top:86px"><svg width="12" height="12"><rect x="1" y="5" width="10" height="7" fill="#222"/><path d="M3 5V3.5a3 3 0 016 0V5" fill="none" stroke="#222" stroke-width="1.6"/></svg>Expired</div>
    <div class="pay abs"><svg width="14" height="10"><rect x=".5" y=".5" width="13" height="9" fill="none" stroke="#222"/><circle cx="7" cy="5" r="2" fill="#222"/></svg>$31000</div>
    <div class="time abs"><svg width="12" height="12"><circle cx="6" cy="6" r="5" fill="none" stroke="currentColor" stroke-width="1.6"/><path d="M6 3v3h2" stroke="currentColor" fill="none"/></svg>Full Time</div>
    <div class="view btn btn-outline abs" style="top:36px">View More</div>
  </div>
</section>

<section class="testimonials">
  <h2 class="section-title abs" style="left:0;width:1192px;text-align:center;top:2187px">TESTIMONIALS</h2>

  <div class="testi abs" style="left:84px">
    <div class="avatar abs" role="img" aria-label="Portrait of client"></div>
    <p class="abs" style="top:118px">“I was highly impressed by the professionalism shown during my interview process. It was less an interview and more of a conversation with the recruiter. I felt comfortable sharing my previous management experience”</p>
    <div class="name abs">- Marla Keene</div>
  </div>
  <div class="testi abs" style="left:432px">
    <div class="avatar abs" role="img" aria-label="Portrait of client"></div>
    <p class="abs">I didn’t even need training. I couldn’t have asked for more than this. It really saves me time and effort. Plorvex is exactly what our business has been lacking. I would be lost without Plorvex</p>
    <div class="name abs">- Tessa Worth</div>
  </div>
  <div class="testi abs" style="left:778px">
    <div class="avatar abs" role="img" aria-label="Portrait of client"></div>
    <p class="abs">I just can’t get enough of Plorvex. I want to get a T-Shirt with Plorvex on it so I can show it off to everyone. This is simply unbelievable</p>
    <div class="name abs">- Evan Lindqvist</div>
  </div>
  <div class="quote abs" style="left:90px">“</div>
  <div class="quote abs" style="left:441px">“</div>
  <div class="quote abs" style="left:789px">“</div>

  <div class="dots3 abs" style="left:578px;top:2651px"><span></span><span class="o"></span><span></span></div>
</section>

<section class="cta abs">
  <h3 class="abs">SEEKING FOR A JOB?</h3>
  <p class="abs">Browse hundreds of job offers and find the best suitable position.</p>
  <div class="b btn abs" style="left:836px;width:126px">Search Jobs</div>
  <div class="b btn abs" style="left:985px;width:122px;text-transform:uppercase">Add a Resume</div>
</section>

<footer class="footer abs">
  <div class="brand abs">Plorvex</div>
  <p class="about abs body-font">Lorem ipsum dolor sit amet, consectetur adipiscing elit, sed do eiusmod tempor didunt ut labore et dolore magna aliqua.</p>

  <h4 class="abs" style="left:468px">Candidates</h4>
  <ul class="abs body-font" style="left:468px">
    <li>Browse Jobs</li><li>Browse Categories</li><li>Candidate Profile</li><li>Edit Resume</li><li>Saved Jobs</li>
  </ul>

  <h4 class="abs" style="left:674px">Quick Links</h4>
  <ul class="abs body-font" style="left:674px">
    <li>Home</li><li>Industries</li><li>Jobs</li><li>Contact Us</li>
  </ul>

  <h4 class="abs" style="left:862px">Contact Us</h4>
  <ul class="abs body-font" style="left:862px">
    <li>18 Calder Lane, Apt.</li><li>7 Fairview, NY 10090 USA</li><li>+1 800 555 0142</li><li>hello@plorvex.com</li>
  </ul>

  <div class="legal abs">Plorvex © 2020. All rights reserved.&nbsp; Site Map &nbsp;&nbsp;| &nbsp;&nbsp;Cookies &nbsp;&nbsp;| &nbsp;&nbsp;Legal &nbsp;&nbsp;| &nbsp;&nbsp;Privacy</div>
</footer>

</body>
</html>
```